BOLD & MINIMALIST DESIGN NEEDED

We want a very bold but minimalistic business card design that is impactful and utilizes both sides of the business card. Our current logo is included for your use.

We want bold fonts and good use of negative space. We don't want the logo to overpower the design.

Target Market(s)

Professionals who are building new commercial buildings.

Industry/Entity Type

Construction

Contact Information for Business Card

Name, Title, email, office phone, cell phone, website

Font styles to use
Serif
Sans Serif

Requirements
Must have
• Bold design!

```html
<!DOCTYPE html>
<html lang="en">
<head>
<meta charset="utf-8">
<title>Ridgeway Design + Build — Business Card</title>
<link href="https://fonts.googleapis.com/css2?family=Arimo:wght@400;700&display=swap" rel="stylesheet">
<style>
  :root {
    --backdrop: #9a9a9a;
    --card-light: #f7f7f5;
    --card-dark: #2b2b2b;
    --ink: #1c1c1c;
    --ink-soft: #2e2e2e;
    --accent: #7dc13b;
    --white: #ffffff;
  }
  * { box-sizing: border-box; margin: 0; padding: 0; }
  html, body {
    width: 1200px;
    height: 1050px;
    overflow: hidden;
    background: var(--backdrop);
    font-family: "Arimo", Arial, sans-serif;
  }
  .canvas {
    position: relative;
    width: 1200px;
    height: 1050px;
  }
  .card {
    position: absolute;
    left: 250px;
    width: 700px;
    height: 400px;
    border-radius: 22px;
    overflow: hidden;
  }
  .card--front { top: 90px; background: var(--card-light); color: var(--ink); }
  .card--back  { top: 560px; background: var(--card-dark); color: var(--white); }

  /* front */
  .brand-mark {
    position: absolute;
    top: 92px;
    right: 80px;
    display: flex;
    align-items: center;
    gap: 12px;
  }
  .brand-mark__square {
    width: 26px;
    height: 26px;
    background: var(--accent);
  }
  .brand-mark__name {
    font-weight: 700;
    font-size: 30px;
    letter-spacing: 1px;
    color: var(--ink);
  }
  .identity {
    position: absolute;
    left: 66px;
    top: 180px;
  }
  .identity__name {
    font-weight: 700;
    font-size: 30px;
    letter-spacing: 0.5px;
    text-transform: uppercase;
  }
  .identity__title {
    font-size: 20px;
    color: var(--accent);
    margin-top: 2px;
  }
  .identity__email {
    font-size: 19px;
    color: var(--ink-soft);
    margin-top: 10px;
  }
  .contact-row {
    position: absolute;
    left: 66px;
    bottom: 58px;
    display: flex;
    align-items: center;
    gap: 30px;
    font-size: 19px;
    color: var(--ink-soft);
    line-height: 1.3;
  }
  .contact-row__divider {
    width: 1px;
    height: 62px;
    background: var(--ink-soft);
  }
  .contact-row__item {
    display: flex;
    align-items: center;
    gap: 10px;
  }
  .contact-row__item svg { width: 16px; height: 16px; fill: var(--ink); }

  /* back */
  .back-brand {
    position: absolute;
    inset: 0;
    display: flex;
    align-items: center;
    justify-content: center;
    gap: 18px;
  }
  .back-brand__square {
    width: 40px;
    height: 40px;
    background: var(--accent);
  }
  .back-brand__name {
    font-weight: 700;
    font-size: 46px;
    letter-spacing: 2px;
    text-transform: uppercase;
    color: var(--white);
  }
</style>
</head>
<body>
<div class="canvas">

  <section class="card card--front" aria-label="Card front">
    <div class="brand-mark">
      <span class="brand-mark__square"></span>
      <span class="brand-mark__name">RIDGEWAY</span>
    </div>

    <div class="identity">
      <h1 class="identity__name">Nora Castell</h1>
      <p class="identity__title">President</p>
      <p class="identity__email">hello@ridgewaybuild.com</p>
    </div>

    <div class="contact-row">
      <address class="contact-row__address" style="font-style:normal">
        2710 Alder Crest Road<br>Millbrook, NY 12545
      </address>
      <span class="contact-row__divider"></span>
      <div class="contact-row__links">
        <p class="contact-row__item">
          <svg viewBox="0 0 24 24" aria-hidden="true"><path d="M6.6 10.8a15.1 15.1 0 0 0 6.6 6.6l2.2-2.2a1 1 0 0 1 1-.25 11.4 11.4 0 0 0 3.6.57 1 1 0 0 1 1 1V20a1 1 0 0 1-1 1A17 17 0 0 1 3 4a1 1 0 0 1 1-1h3.5a1 1 0 0 1 1 1c0 1.25.2 2.45.57 3.6a1 1 0 0 1-.25 1z"/></svg>
          (555) 0142-7781
        </p>
        <p class="contact-row__item">
          <svg viewBox="0 0 24 24" aria-hidden="true"><circle cx="12" cy="12" r="10"/><path d="M2 12h20M12 2c3 3 3 17 0 20M12 2c-3 3-3 17 0 20" stroke="#f7f7f5" stroke-width="1.6" fill="none"/></svg>
          www.ridgewaybuild.com
        </p>
      </div>
    </div>
  </section>

  <section class="card card--back" aria-label="Card back">
    <div class="back-brand">
      <span class="back-brand__square"></span>
      <span class="back-brand__name">Ridgeway Design + Build</span>
    </div>
  </section>

</div>
</body>
</html>
```